Business card design Needed for new logo / Construction business, home extensions and new builds

We need a business card design using our new logo files which i will attach to this project :)

We are a small construction business specialising in home extensions, new builds and property development. We are very ambitious and would appreciate professional and elegant designs for our new business card.

Very serious about using the services on MakerQuarry and recently acquired our new logo from here :)

Please get involved, i will feedback when i can as i am very busy but can respond daily, thanks

Target Market(s)

People that want to build onto their houses, new building developments or adding too their existing property

Industry/Entity Type

Construction

Contact Information for Business Card

Renwick Tolliver Construction, Lionel Ashby (Managing Director), Tel 07822254961, email - info@renwick-tolliver, www.renwick-tolliver.co.uk

Colors

Designer to choose colors to be used in the design.

Requirements
Must have
• I like a deep grey on the back please. A lot of you have provided black from and back, try mixing things up a little. The black looks cool 😎 Thanks

```html
<!DOCTYPE html>
<html lang="en">
<head>
<meta charset="utf-8">
<title>Renwick Tolliver Construction – Business Card</title>
<link rel="stylesheet" href="https://fonts.googleapis.com/css2?family=Montserrat:wght@400;500;600&display=swap">
<style>
  :root {
    --backdrop: #3b3b3c;
    --card-white: #ffffff;
    --card-black: #0c0c0c;
    --card-deep: #161616;
    --gold: #c9971f;
    --gold-light: #e6b845;
    --silver: #c9cbcd;
    --text-light: #f2f2f2;
    --divider: #4a4a4a;
  }
  * { box-sizing: border-box; margin: 0; padding: 0; }
  html, body {
    width: 1200px; height: 1200px; overflow: hidden;
    background: var(--backdrop);
    font-family: "Montserrat", Arial, sans-serif;
  }
  .stage {
    width: 1200px; height: 1200px;
    display: flex; flex-direction: column; align-items: center; justify-content: center;
    gap: 40px;
  }
  .card {
    width: 960px; height: 548px;
    border-radius: 38px;
    overflow: hidden;
    position: relative;
    box-shadow: 0 18px 40px rgba(0,0,0,.45);
  }

  /* Front */
  .card-front { background: var(--card-white); }
  .front-top {
    height: 300px;
    display: flex; align-items: center; justify-content: center; gap: 18px;
  }
  .brand-mark { width: 26px; height: 26px; background: var(--gold); }
  .brand-name {
    font-weight: 600; font-size: 34px; letter-spacing: 3px;
    text-transform: uppercase; color: var(--gold);
  }
  .gold-rule { height: 8px; background: var(--gold); }
  .white-gap { height: 8px; background: var(--card-white); }
  .front-bottom {
    position: absolute; left: 0; right: 0; top: 316px; bottom: 0;
    background: var(--card-black);
    display: flex; align-items: center;
  }
  .person {
    width: 50%; padding-left: 90px;
    border-left: none;
  }
  .person-inner { border-left: 7px solid var(--gold); padding-left: 18px; }
  .person-name {
    font-weight: 600; font-size: 30px; color: var(--gold-light);
    text-transform: uppercase; letter-spacing: .5px;
  }
  .person-role {
    font-weight: 400; font-size: 20px; color: var(--text-light);
    text-transform: uppercase; letter-spacing: 1px; margin-top: 4px;
  }
  .column-divider { width: 1px; height: 130px; background: var(--divider); }
  .contacts { padding-left: 50px; list-style: none; }
  .contact {
    display: flex; align-items: center; gap: 14px;
    font-size: 21px; color: var(--text-light); line-height: 1.9;
  }
  .contact svg { width: 24px; height: 24px; flex: none; }

  /* Back */
  .card-back {
    background: linear-gradient(120deg, #1a1a1a 0%, var(--card-deep) 45%, #0e0e0e 100%);
    display: flex; align-items: center; justify-content: center; gap: 22px;
  }
  .card-back .brand-name { font-size: 44px; color: var(--silver); }
  .card-back .brand-mark { width: 32px; height: 32px; background: var(--gold); }
</style>
</head>
<body>
<main class="stage">
  <section class="card card-front">
    <div class="front-top">
      <span class="brand-mark"></span>
      <span class="brand-name">Renwick Tolliver Construction</span>
    </div>
    <div class="gold-rule"></div>
    <div class="white-gap"></div>
    <div class="front-bottom">
      <div class="person">
        <div class="person-inner">
          <p class="person-name">Lionel Ashby</p>
          <p class="person-role">Managing Director</p>
        </div>
      </div>
      <div class="column-divider"></div>
      <ul class="contacts">
        <li class="contact">
          <svg viewBox="0 0 24 24" aria-hidden="true"><path fill="#c9971f" d="M6.6 10.8a15.1 15.1 0 0 0 6.6 6.6l2.2-2.2a1 1 0 0 1 1-.25 11.4 11.4 0 0 0 3.6.57 1 1 0 0 1 1 1V20a1 1 0 0 1-1 1A17 17 0 0 1 3 4a1 1 0 0 1 1-1h3.5a1 1 0 0 1 1 1c0 1.25.2 2.45.57 3.57a1 1 0 0 1-.25 1z"/></svg>
          +44 7822 254 961
        </li>
        <li class="contact">
          <svg viewBox="0 0 24 24" aria-hidden="true"><rect x="2" y="5" width="20" height="14" rx="1.5" fill="#c9971f"/><path d="M3 6l9 7 9-7" fill="none" stroke="#0c0c0c" stroke-width="1.6"/></svg>
          info@renwick-tolliver.co.uk
        </li>
        <li class="contact">
          <svg viewBox="0 0 24 24" aria-hidden="true"><g fill="none" stroke="#c9971f" stroke-width="1.7"><circle cx="12" cy="12" r="9.5"/><ellipse cx="12" cy="12" rx="4" ry="9.5"/><path d="M2.5 12h19M4 7h16M4 17h16"/></g></svg>
          www.renwick-tolliver.co.uk
        </li>
      </ul>
    </div>
  </section>

  <section class="card card-back">
    <span class="brand-mark"></span>
    <span class="brand-name">Renwick Tolliver Construction</span>
  </section>
</main>
</body>
</html>
```